Luxury Business Card Design for High-End Window Treatments

Gilded Slatworks
Custom Plantation Shutters & Architectural Shading Systems

⸻

BACK

Daniel Trevick
Owner

Custom Interior & Exterior Window Treatments

919-555-0148
gildedslatworks.com

I have included a picture that I’m hoping we can use on the back, but I’m also wondering if you can get rid of the ladder? Should we get rid of shutters , shades and blinds underneath Gilded Slatworks?

Target Market(s)

High-end residential homeowners, custom home builders, architects, interior designers, and luxury renovation clients seeking premium plantation shutters and motorized architectural shading systems.

Industry/Entity Type

Custom Window treatments

Contact Information for Business Card

Front Gilded Slatworks Custom Plantation Shutters Motorized Architectural Shading Systems BACK Daniel Trevick Owner 919-555-0148 GildedSlatworks.com Custom Interior & Exterior Window Treatments By Appointment

Requirements
Nice to have
• Not 100% sure on nice to halves or the color but you can definitely check out my website to get a better understanding of what I’m trying to do

```html
<!DOCTYPE html>
<html lang="en">
<head>
<meta charset="utf-8">
<title>Gilded Slatworks – Business Card</title>
<link href="https://fonts.googleapis.com/css2?family=Arvo:wght@700&family=Poppins:wght@400&family=Prata&display=swap" rel="stylesheet">
<style>
  :root {
    --page-bg: #1e1e1e;
    --card-black: #050505;
    --gold: #c9ac55;
    --gold-soft: #b89a4a;
    --white: #f4f4f4;
    --sky-top: #3f86e0;
    --sky-low: #8fbbe8;
    --wall: #4a5462;
    --trim: #dcdcd6;
    --hedge: #3f5a30;
  }
  * { margin: 0; padding: 0; box-sizing: border-box; }
  html, body {
    width: 1200px; height: 1015px; overflow: hidden;
    background: var(--page-bg);
  }
  .canvas {
    width: 1200px; height: 1015px;
    display: flex; flex-direction: column; align-items: center; justify-content: center;
    gap: 50px;
  }
  .card {
    position: relative;
    width: 620px; height: 354px;
    background: var(--card-black);
    overflow: hidden;
    box-shadow: 0 12px 30px rgba(0,0,0,.55);
  }

  /* Front */
  .card-front { display: flex; flex-direction: column; align-items: center; justify-content: center; }
  .brand-name {
    font-family: "Prata", serif;
    color: var(--gold);
    font-size: 54px; line-height: 1.05; text-align: center;
    font-weight: 400;
  }
  .service-list {
    list-style: none; margin-top: 30px;
    font-family: "Prata", serif; color: var(--white);
    font-size: 16px; line-height: 1.45;
  }
  .service-list li { display: flex; align-items: center; gap: 10px; }
  .service-list li::before {
    content: ""; width: 8px; height: 8px; border-radius: 50%;
    border: 1.5px solid var(--gold); flex: none;
  }
  .service-list li:nth-child(2) { padding-left: 14px; }
  .service-list li:nth-child(3) { padding-left: 28px; }

  /* Back */
  .photo-disc { position: absolute; left: 0; top: 0; }
  .contact-block { position: absolute; left: 44px; top: 118px; }
  .person-name {
    font-family: "Arvo", serif; font-weight: 700;
    color: var(--gold); font-size: 28px; line-height: 1;
  }
  .person-role {
    font-family: "Poppins", sans-serif; color: var(--white);
    font-size: 17px; line-height: 1.2; margin-top: 2px;
  }
  .contact-lines { margin-top: 38px; display: flex; flex-direction: column; gap: 6px; }
  .contact-line {
    display: flex; align-items: center; gap: 12px;
    font-family: "Poppins", sans-serif; color: var(--white);
    font-size: 19px; line-height: 1.2;
  }
  .contact-line svg { width: 18px; height: 18px; flex: none; }
  .tagline {
    position: absolute; left: 96px; top: 268px;
    font-family: "Prata", serif; color: var(--gold);
    font-size: 17px; line-height: 1.3;
  }
</style>
</head>
<body>
<main class="canvas">

  <section class="card card-front">
    <h1 class="brand-name">Gilded<br>Slatworks</h1>
    <ul class="service-list">
      <li>Gilded Slatworks Custom</li>
      <li>Plantation Shutters Motorized</li>
      <li>Architectural Shading Systems</li>
    </ul>
  </section>

  <section class="card card-back">
    <svg class="photo-disc" width="620" height="354" viewBox="0 0 620 354">
      <defs>
        <linearGradient id="porch-tones" x1="0" y1="0" x2="0" y2="1">
          <stop offset="0" stop-color="var(--sky-top)"/>
          <stop offset="0.3" stop-color="var(--sky-low)"/>
          <stop offset="0.45" stop-color="var(--trim)"/>
          <stop offset="0.55" stop-color="var(--wall)"/>
          <stop offset="0.85" stop-color="var(--wall)"/>
          <stop offset="1" stop-color="var(--hedge)"/>
        </linearGradient>
      </defs>
      <circle cx="590" cy="140" r="236" fill="var(--gold)"/>
      <circle cx="594" cy="138" r="230" fill="var(--card-black)"/>
      <circle cx="600" cy="136" r="222" fill="url(#porch-tones)" role="img"
              aria-label="Photo of a covered porch with white columns and motorized exterior shades"/>
    </svg>

    <div class="contact-block">
      <h2 class="person-name">Daniel Trevick</h2>
      <p class="person-role">Owner</p>
      <div class="contact-lines">
        <p class="contact-line">
          <svg viewBox="0 0 24 24" fill="none" stroke="var(--gold)" stroke-width="2.2" stroke-linecap="round" stroke-linejoin="round">
            <path d="M5 3h4l2 5-2.5 1.5a11 11 0 0 0 6 6L16 13l5 2v4a2 2 0 0 1-2 2A16 16 0 0 1 3 5a2 2 0 0 1 2-2z"/>
          </svg>
          919-555-0148
        </p>
        <p class="contact-line">
          <svg viewBox="0 0 24 24" fill="none" stroke="var(--gold)" stroke-width="2">
            <circle cx="12" cy="12" r="9.5"/>
            <ellipse cx="12" cy="12" rx="4" ry="9.5"/>
            <path d="M2.5 12h19M4 7h16M4 17h16"/>
          </svg>
          GildedSlatworks.com
        </p>
      </div>
    </div>

    <p class="tagline">Custom Interior &amp;<br>Exterior Window<br>Treatments By Appointment</p>
  </section>

</main>
</body>
</html>
```